full stationary design for a modern sleek design company

we are a design company that does modern minimalistic interior design works as well as other design services for high end clients.
we need a full stationary design including and not limited to (double sided business card, letter head, envelopes, documents folder...etc) that reflects the modern style design we do.
sleek modern and minimalistic is the requirements.
Updates

please use the latest attached files as there was a slight modification on the logo Added Wednesday, March 1, 2017

minor update on the logo files in JPG and PSD has been updated kindly follow the new attachments. Added Thursday, March 2, 2017

Target Market(s)

modern minimalist clients

Industry/Entity Type

Design Agency

Requirements
Must have
• the logo
Nice to have
• i like the colors in the colored 3D logo attached
Should not have
• too many colors

```html
<!DOCTYPE html>
<html lang="en">
<head>
<meta charset="utf-8">
<title>Norvale Interiors — Business Card</title>
<link href="https://fonts.googleapis.com/css2?family=Open+Sans:wght@400;600;700&display=swap" rel="stylesheet">
<style>
  :root {
    --bg: #3a3a3a;
    --orange: #f0891c;
    --charcoal: #2e2e2e;
    --card-white: #f7f7f7;
    --ink: #333333;
  }
  * { margin: 0; padding: 0; box-sizing: border-box; }
  html, body {
    width: 1200px; height: 750px; overflow: hidden;
    background: var(--bg);
    font-family: "Open Sans", sans-serif;
  }
  .stage { position: relative; width: 1200px; height: 750px; }

  .card {
    position: absolute; top: 228px;
    width: 461px; height: 262px;
    border-radius: 11px; overflow: hidden;
  }
  .card--front { left: 124px; background: var(--card-white); }
  .card--back { left: 618px; background: var(--charcoal); }

  .card__band { position: absolute; inset: 0; }

  .brand {
    position: absolute; display: flex; align-items: center; gap: 10px;
    font-weight: 700; font-size: 21px; letter-spacing: 2px; white-space: nowrap;
  }
  .brand__mark { width: 26px; height: 26px; background: var(--orange); }
  .card--front .brand { left: 68px; top: 62px; color: var(--charcoal); }
  .card--back .brand { left: 74px; top: 116px; color: var(--orange); }

  .person {
    position: absolute; right: 250px; top: 165px;
    text-align: right; color: var(--ink); font-size: 12.5px; line-height: 17.5px;
  }
  .person__name { font-size: 17px; font-weight: 600; line-height: 22px; }

  .divider {
    position: absolute; left: 226px; top: 168px;
    width: 1px; height: 72px; background: var(--ink);
  }

  .contact {
    position: absolute; left: 238px; top: 167px;
    list-style: none; color: var(--ink); font-size: 12.5px; line-height: 17.6px;
  }
  .contact li { display: flex; align-items: center; gap: 7px; }
  .contact svg { width: 11px; height: 11px; fill: var(--charcoal); flex: none; }
</style>
</head>
<body>
<main class="stage">

  <section class="card card--front" aria-label="Business card front">
    <svg class="card__band" viewBox="0 0 461 262" aria-hidden="true">
      <path d="M0 147 H405 Q445 147 461 118 V262 H0 Z" fill="var(--orange)"/>
      <path d="M0 143 H405 Q442 143 461 113" fill="none" stroke="var(--charcoal)" stroke-width="4"/>
    </svg>

    <div class="brand"><span class="brand__mark"></span>NORVALE INTERIORS</div>

    <div class="person">
      <p class="person__name">ELENA MARSH</p>
      <p>CEO&amp;Founder</p>
      <p>214 Willow Crest Road</p>
      <p>Fairbanks, Alaska 99701</p>
    </div>

    <div class="divider"></div>

    <ul class="contact">
      <li><svg viewBox="0 0 24 24"><path d="M6.6 10.8a15 15 0 0 0 6.6 6.6l2.2-2.2c.3-.3.7-.4 1-.2 1.1.4 2.3.6 3.6.6.6 0 1 .4 1 1V20c0 .6-.4 1-1 1A17 17 0 0 1 3 4c0-.6.4-1 1-1h3.5c.6 0 1 .4 1 1 0 1.3.2 2.5.6 3.6.1.3 0 .7-.2 1z"/></svg>(555) 210 4876</li>
      <li><svg viewBox="0 0 24 24"><path d="M7 1h10a2 2 0 0 1 2 2v18a2 2 0 0 1-2 2H7a2 2 0 0 1-2-2V3a2 2 0 0 1 2-2zm0 3v15h10V4z"/></svg>(555) 732 1095</li>
      <li><svg viewBox="0 0 24 24"><path d="M2 5h20v14H2zm2 2v.5l8 5 8-5V7zm0 2.8V17h16V9.8l-8 5z"/></svg>elena@norvale.com</li>
      <li><svg viewBox="0 0 24 24"><path d="M12 2a10 10 0 1 0 0 20 10 10 0 0 0 0-20zm-1 17.9A8 8 0 0 1 4.2 10L9 14.8v1a2 2 0 0 0 2 2zm6.9-2.5A2 2 0 0 0 16 16h-1v-3a1 1 0 0 0-1-1H8v-2h2a1 1 0 0 0 1-1V7h2a2 2 0 0 0 2-2v-.4a8 8 0 0 1 2.9 12.8z"/></svg>www.norvale.com</li>
    </ul>
  </section>

  <section class="card card--back" aria-label="Business card back">
    <div class="brand"><span class="brand__mark"></span>NORVALE INTERIORS</div>
  </section>

</main>
</body>
</html>
```